Business Cards for new orthopaedic surgery practice

My husband and I are starting our own orthopaedic surgery practice. We are looking for a business card that is uniform, but one will have my name/title and the other will have his. You can just create one design with my name on it for now. But when I choose your design as the winning design I will ask that you add another copy with his name/title.

We are looking for classy, simple, elite all in one. We like dark blues/a little gold/yellow. Something that goes with our logo. We want our logo incorporated. Here is all the info you need:
Business name: RV Bone & Vitality Center
Location: 38517 North Willowmere Ave
Coral Springs, FL 33071
Phone: 954-218-4063
Fax: 954-582-7341
Email: info@myrvbonecare.example

Names: Lydia Vance, M.D.
Board Certified Hand and Upper Extremity Surgeon

Ebo Dansu, M.D.
Board Certified Hip & Knee Replacement/General Orthopaedic Surgeon

Can decide what you want to put on the back. Maybe a slogan:
Precise Care. Lasting Strength

I am just going to upload our logo. The only thing is if we select you as the winning design, the location, and phone numbers may change. We will need your help to update that once fully solidified.

Industry/Entity Type

Medical

Contact Information for Business Card

Colors
0054AA
0677BA
7BADD7
CADEEF
E8F1F8
0094D4
00A9DD
6FCCEA
C7EBF8
E9F6FB

Requirements
Must have
• class, appeal,
Should not have
• We want to air on the side of masculine if we are looking at masculine vs. feminine feel. But we still want it classy, sophisticated, and something we will love

```html
<!DOCTYPE html>
<html lang="en">
<head>
<meta charset="utf-8">
<title>RV Bone &amp; Vitality Center — Business Card</title>
<link href="https://fonts.googleapis.com/css2?family=Cinzel:wght@600&family=Roboto:wght@400;500&display=swap" rel="stylesheet">
<style>
  :root {
    --navy: #2f4a93;
    --ink-navy: #1d3f8f;
    --cyan: #00a9dd;
    --paper: #f4f4f4;
    --text: #333333;
    --stage: #e4e4e4;
    --edge: #0094d4;
    --white: #ffffff;
  }
  * { box-sizing: border-box; margin: 0; padding: 0; }
  html, body { width: 1200px; height: 884px; overflow: hidden; }
  body {
    background: var(--stage);
    position: relative;
    font-family: "Roboto", Arial, sans-serif;
  }
  .card {
    position: absolute;
    border-bottom: 3px solid var(--edge);
    box-shadow: 0 14px 30px rgba(0,0,0,0.18);
  }

  /* Front: blue with practice name and slogan */
  .card-front {
    left: 70px; top: 290px; width: 540px; height: 309px;
    background: var(--navy);
    display: flex; flex-direction: column; align-items: center; justify-content: center;
    gap: 20px;
  }
  .brand {
    display: flex; align-items: center; gap: 12px;
    font-family: "Roboto", Arial, sans-serif; font-weight: 500;
    white-space: nowrap;
  }
  .brand-dot { border-radius: 50%; flex: none; background: var(--cyan); }
  .card-front .brand { color: var(--white); font-size: 30px; }
  .card-front .brand-dot { width: 16px; height: 16px; }
  .slogan {
    font-family: "Roboto", Arial, sans-serif; font-weight: 400;
    color: var(--cyan); font-size: 13px; letter-spacing: 3px; text-transform: uppercase;
  }

  /* Back: white with contact details */
  .card-back {
    left: 720px; top: 150px; width: 330px; height: 578px;
    background: var(--paper);
    padding: 70px 36px 0 40px;
  }
  .card-back .brand { color: var(--ink-navy); font-size: 17px; justify-content: center; }
  .card-back .brand-dot { width: 11px; height: 11px; }
  .person { margin-top: 62px; }
  .person-name {
    font-family: "Cinzel", Georgia, serif; font-weight: 600;
    color: var(--ink-navy); font-size: 19px; letter-spacing: 0.5px;
  }
  .person-title { color: var(--cyan); font-size: 15.5px; line-height: 1.25; margin-top: 4px; }
  .contact { list-style: none; margin-top: 36px; color: var(--text); font-size: 15.5px; }
  .contact li { display: flex; align-items: flex-start; gap: 10px; line-height: 1.3; margin-bottom: 4px; }
  .contact li.address { margin-bottom: 22px; }
  .icon { width: 16px; height: 16px; flex: none; margin-top: 2px; fill: var(--ink-navy); }
</style>
</head>
<body>
  <section class="card card-front" aria-label="Card front">
    <div class="brand"><span class="brand-dot"></span>RV Bone &amp; Vitality Center</div>
    <p class="slogan">Precise Care. Lasting Strength</p>
  </section>

  <section class="card card-back" aria-label="Card back">
    <div class="brand"><span class="brand-dot"></span>RV Bone &amp; Vitality Center</div>
    <div class="person">
      <h1 class="person-name">LYDIA VANCE, M.D.</h1>
      <p class="person-title">Board Certified Hand and<br>Upper Extremity Surgeon</p>
    </div>
    <ul class="contact">
      <li class="address">
        <svg class="icon" viewBox="0 0 16 16"><path d="M8 0a5.5 5.5 0 0 0-5.5 5.5C2.5 10 8 16 8 16s5.5-6 5.5-10.5A5.5 5.5 0 0 0 8 0zm0 8a2.5 2.5 0 1 1 0-5 2.5 2.5 0 0 1 0 5z"/></svg>
        <span>38517 North Willowmere Ave<br>Coral Springs, FL 33071</span>
      </li>
      <li>
        <svg class="icon" viewBox="0 0 16 16"><path d="M3.6 1l2.3 3-1.3 1.6a9 9 0 0 0 5.8 5.8L12 10.1l3 2.3-1.2 2.6C7.5 15.3.7 8.5 1 2.2z"/></svg>
        <span>954-218-4063</span>
      </li>
      <li>
        <svg class="icon" viewBox="0 0 16 16"><rect x="4" y="1" width="8" height="4"/><rect x="1" y="6" width="14" height="6" rx="1"/><rect x="4" y="10" width="8" height="5" fill="#fff" stroke="#1d3f8f"/></svg>
        <span>954-582-7341</span>
      </li>
      <li>
        <svg class="icon" viewBox="0 0 16 16"><rect x="1" y="3" width="14" height="10" rx="1"/><path d="M1.5 3.5L8 9l6.5-5.5" fill="none" stroke="#fff" stroke-width="1.2"/></svg>
        <span>info@myrvbonecare.example</span>
      </li>
      <li>
        <svg class="icon" viewBox="0 0 16 16"><circle cx="8" cy="8" r="7"/><path d="M1 8h14M8 1c3 3 3 11 0 14M8 1c-3 3-3 11 0 14" fill="none" stroke="#fff" stroke-width="1"/></svg>
        <span>www.lvancehand.example</span>
      </li>
    </ul>
  </section>
</body>
</html>
```